Upmarket Dessert Lounge needs a Business Card Design

We are an upmarket dessert lounge needing a business card to match our image.

We want something that is simple yet beautiful, feminine, classy, sophisticated and elegant. We want it to stand out and don't mind if it is bold.

The design should include our logo and colours of red or maroon with gold highlights. We don't mind if black is used.

Marlow & Quince

Target Market(s)

For those who like to indulge or treat themselves and give in to their temptations on good quality desserts.

Industry/Entity Type

Business

Requirements
Must have
• Must include our logo and our name

Marlow & Quince

M & Q

```html
<!DOCTYPE html>
<html lang="en">
<head>
<meta charset="utf-8">
<title>Marlow &amp; Quince — Business Card</title>
<link rel="stylesheet" href="https://fonts.googleapis.com/css2?family=Libre+Baskerville:wght@400;700&family=PT+Sans:wght@400&display=swap">
<style>
  :root {
    --backdrop: #ece7e3;
    --card: #ffffff;
    --maroon: #7a1518;
    --gold: #f1c99a;
    --blush: #e6d2d3;
    --blush-edge: #f3e6e6;
    --ink: #3a3a3a;
    --ink-soft: #555555;
  }
  * { margin: 0; padding: 0; box-sizing: border-box; }
  html, body {
    width: 1200px; height: 758px; overflow: hidden;
    background: var(--backdrop);
  }
  .canvas {
    position: relative; width: 1200px; height: 758px;
    display: flex; align-items: center; justify-content: center; gap: 60px;
  }
  .card {
    position: relative; width: 520px; height: 300px;
    background: var(--card); border-radius: 26px;
    box-shadow: 0 6px 18px rgba(0,0,0,0.18);
    overflow: hidden;
  }
  /* Front */
  .brand-name {
    position: absolute; left: 34px; top: 74px; width: 230px;
    font-family: "Libre Baskerville", serif; font-weight: 400;
    font-size: 24px; line-height: 1.25; letter-spacing: 1px;
    color: var(--maroon); text-align: center;
  }
  .address {
    position: absolute; left: 312px; top: 52px;
    font-family: "PT Sans", sans-serif; font-size: 13px; line-height: 1.4;
    color: var(--ink);
  }
  .contact-band {
    position: absolute; left: 40px; top: 176px; width: 470px; height: 96px;
    background: var(--blush); border-radius: 48px;
    box-shadow: 0 0 0 4px var(--blush-edge);
  }
  .person {
    position: absolute; right: 280px; top: 200px; text-align: right;
    font-family: "Libre Baskerville", serif; color: var(--ink);
  }
  .person-name { font-size: 16px; font-weight: 700; letter-spacing: 2px; }
  .person-title { font-family: "PT Sans", sans-serif; font-size: 12px; letter-spacing: 1px; color: var(--ink-soft); }
  .divider {
    position: absolute; left: 250px; top: 192px; width: 1px; height: 54px;
    background: var(--ink-soft);
  }
  .contact-list {
    position: absolute; left: 260px; top: 184px; list-style: none;
    font-family: "PT Sans", sans-serif; font-size: 12.5px; line-height: 17px;
    color: var(--ink);
  }
  .contact-list li { display: flex; align-items: center; gap: 5px; }
  .contact-list svg { width: 10px; height: 10px; fill: var(--ink); flex: none; }
  /* Back */
  .monogram {
    position: absolute; left: 0; right: 0; top: 70px; text-align: center;
    font-family: "Libre Baskerville", serif; font-size: 72px;
    color: var(--maroon); letter-spacing: 2px;
  }
  .web-address {
    position: absolute; left: 0; right: 0; bottom: 44px; text-align: center;
    font-family: "PT Sans", sans-serif; font-size: 19px; letter-spacing: 3px;
    color: var(--ink);
  }
</style>
</head>
<body>
<main class="canvas">
  <section class="card card-front">
    <div class="brand-name">MARLOW &amp; QUINCE</div>
    <div class="address">Street Name, City Name<br>State Zip Code</div>
    <div class="contact-band"></div>
    <div class="person">
      <div class="person-name">Your name</div>
      <div class="person-title">Title</div>
    </div>
    <div class="divider"></div>
    <ul class="contact-list">
      <li><svg viewBox="0 0 10 10"><path d="M2 0.5 L4 2.5 L3 3.6 Q4 6 6.4 7 L7.5 6 L9.5 8 L8.2 9.5 Q3 9 0.5 1.8 Z"/></svg>555-019-4827</li>
      <li><svg viewBox="0 0 10 10"><path d="M3 0 H7 Q8 0 8 1 V9 Q8 10 7 10 H3 Q2 10 2 9 V1 Q2 0 3 0 Z M3 1.5 V7 H7 V1.5 Z"/></svg>555-019-4827</li>
      <li><svg viewBox="0 0 10 10"><path d="M0 2 H10 V8 H0 Z M0.6 2.4 L5 5.6 L9.4 2.4" stroke="#fff" stroke-width="0.8"/></svg>info@marlowquince.com</li>
      <li><svg viewBox="0 0 10 10"><circle cx="5" cy="5" r="4.5"/><path d="M0.5 5 H9.5 M5 0.5 V9.5 M5 0.5 Q2 5 5 9.5 M5 0.5 Q8 5 5 9.5" stroke="#fff" stroke-width="0.7" fill="none"/></svg>www.marlowquince.com</li>
    </ul>
  </section>
  <section class="card card-back">
    <div class="monogram">M&amp;Q</div>
    <div class="web-address">www.marlowquince.com</div>
  </section>
</main>
</body>
</html>
```